TL - business card

Tallow Partners is an insurance brokerage firm, inovative, proactive, vigorous, which aims to become the leader of the insurance brokers in Anfrica. We should like to get some designs which should be avoided also in Gray / Metallic for the Administration and Orange / Blue for the Managers (ike in the picture sent). The Blue / Green logo is not the correct one, but the source of the file. Please adjust the color accordingly for the business cards. 1 / Orange / Blue 2 / Gray / Metallic We want something classic but which is transmitted strenght, inovation, modernity and most of all, rapidity. We want something start-up like, very punchy and catching eye remaining profesional at the same time. Name: Dorian Whitlock Function: Managing Director Address: N ° 17/18 Rua Veloso - R / C 2B Direita - Bairro Mutamba - Luanda Tel: (+244) 947 582 316 Email: dorian.whitlock@tallow-p.example Website: www.tallow-p. example We want classic in the front and creative, colorfull at the back. The cards will be printed in relief, with very high quality of paper.
Insurance Broker
Colors
Designer to choose colors to be used in the design.

```html
<!DOCTYPE html>
<html lang="en">
<head>
<meta charset="utf-8">
<title>Tallow Partners – Business Card</title>
<link href="https://fonts.googleapis.com/css2?family=Exo+2:wght@500;600&family=Lato:wght@400&display=swap" rel="stylesheet">
<style>
  :root {
    --backdrop: #9a9a9a;
    --card-white: #ffffff;
    --brand-orange: #f26a21;
    --brand-blue: #2aa3dd;
    --ink: #3d3d3d;
    --rule: #b8b8b8;
    --on-orange: #ffffff;
  }
  html, body {
    margin: 0;
    padding: 0;
    width: 1200px;
    height: 802px;
    overflow: hidden;
    background: var(--backdrop);
  }
  .canvas {
    position: relative;
    width: 1200px;
    height: 802px;
  }
  .card {
    position: absolute;
    top: 274px;
    width: 442px;
    height: 264px;
    box-shadow: 2px 4px 8px rgba(0,0,0,0.35);
    overflow: hidden;
  }
  .card-front { left: 136px; background: var(--card-white); }
  .card-back { left: 624px; }

  .brand-mark {
    position: absolute;
    left: 271px;
    top: 45px;
    width: 76px;
    height: 76px;
    box-sizing: border-box;
    border: 5px solid var(--brand-orange);
    border-radius: 50%;
  }
  .brand-name {
    position: absolute;
    right: 31px;
    top: 122px;
    margin: 0;
    font-family: "Exo 2", sans-serif;
    font-weight: 600;
    font-size: 22px;
    letter-spacing: 0.2px;
    color: var(--brand-orange);
    white-space: nowrap;
  }

  .holder {
    position: absolute;
    left: 28px;
    top: 161px;
    right: 31px;
    display: flex;
    align-items: center;
  }
  .holder-name {
    margin: 0;
    font-family: "Exo 2", sans-serif;
    font-weight: 500;
    font-size: 17px;
    white-space: nowrap;
  }
  .holder-name .first { color: var(--brand-orange); }
  .holder-name .last { color: var(--brand-blue); }
  .holder-rule {
    flex: 1;
    height: 1px;
    background: var(--rule);
    margin-left: 9px;
    margin-top: 2px;
  }
  .holder-role {
    position: absolute;
    left: 28px;
    top: 182px;
    margin: 0;
    font-family: "Lato", sans-serif;
    font-size: 12.5px;
    color: var(--ink);
  }

  .contact {
    position: absolute;
    left: 28px;
    top: 210px;
    margin: 0;
    padding: 0;
    list-style: none;
    font-family: "Lato", sans-serif;
    font-size: 12.5px;
    line-height: 16px;
    color: var(--ink);
  }
  .contact li { display: flex; align-items: center; gap: 4px; }
  .contact svg { width: 12px; height: 12px; flex: none; }

  .address {
    position: absolute;
    right: 31px;
    top: 194px;
    margin: 0;
    font-style: normal;
    text-align: right;
    font-family: "Lato", sans-serif;
    font-size: 12.5px;
    line-height: 16px;
    color: var(--ink);
  }

  .back-field {
    position: absolute;
    inset: 0;
    background: radial-gradient(circle at 50% 50%, #f46f25 0%, var(--brand-orange) 70%, #ee661e 100%);
  }
  .back-name {
    position: absolute;
    left: 0;
    right: 0;
    top: 112px;
    margin: 0;
    text-align: center;
    font-family: "Exo 2", sans-serif;
    font-weight: 600;
    font-size: 29px;
    color: var(--on-orange);
    white-space: nowrap;
  }
</style>
</head>
<body>
<main class="canvas">
  <section class="card card-front" aria-label="Business card front">
    <div class="brand-mark" aria-hidden="true"></div>
    <h1 class="brand-name">TALLOW PARTNERS</h1>

    <div class="holder">
      <h2 class="holder-name"><span class="first">DORIAN</span> <span class="last">WHITLOCK</span></h2>
      <span class="holder-rule" aria-hidden="true"></span>
    </div>
    <p class="holder-role">Managing Director</p>

    <ul class="contact">
      <li>
        <svg viewBox="0 0 12 12" aria-hidden="true"><path d="M1 4.5 C1 2.5 3 1.5 6 1.5 C9 1.5 11 2.5 11 4.5 L8.5 5 L8 3.8 L4 3.8 L3.5 5 Z M2.5 6 L9.5 6 L10.5 10.5 L1.5 10.5 Z" fill="var(--brand-orange)"/></svg>
        <span>(+244) 947 582 316</span>
      </li>
      <li>
        <svg viewBox="0 0 12 12" aria-hidden="true"><rect x="0.5" y="2.5" width="11" height="8" fill="var(--brand-orange)"/><path d="M0.5 2.5 L6 7 L11.5 2.5" fill="none" stroke="#fff" stroke-width="1"/></svg>
        <span>dorian.whitlock@tallow-p.example</span>
      </li>
    </ul>

    <address class="address">
      N ° 17/18 Rua Veloso - R / C<br>
      2B Direita<br>
      Bairro Mutamba - Luanda
    </address>
  </section>

  <section class="card card-back" aria-label="Business card back">
    <div class="back-field" role="img" aria-label="Orange background with a faint repeating brand pattern"></div>
    <h2 class="back-name">TALLOW PARTNERS</h2>
  </section>
</main>
</body>
</html>
```